A Techincal Author needs a site to promote his Programming Books

The StudyAlong series is a collection of books focusing on building the same app with different technologies. The purpose of this project is to design a web site home page that can be used to sell the books.

Expected Deliverables
• StudyAlong Logo as Illustrator file
• Master graphic design files for any relevant web assets
• HTML and CSS for home page, if applicable

Target Market(s)

The target market for our series is web programmers. They are people who have some experience, but want to learn a new tool. Programmers are analytical, logical people who like structure in the things they do.

Here are some things our customers like:

• Chirply / Postbox
• Crown of Ashes / Hollow Tide / Salt Hollow
• SmartPhones, Tablets, Stridelets, and other tech gadgets.

The design should try to speak to that market.

Requirements
Must have
• The primary tasks for this project are:
• 1) Create "Study Along" Logo.
• * All “NetPivot” properties use a similar logo approach, with the NetPivot ball icon on the left, a reflection below it. The company name is on the right, roughly the same size as the ball icon. A tag line underneath the company name, roughly the same size as the reflection.
• * Company Name: Study Along
• * Tagline: Knowledge to Boost Your Career
• * Logo color is up to the discretion of the designer, but should be compatible with the site design.
• * Sample Logos for other NetPivot properties in Illustrator format are available as attachments to this project.
• 2) Design the Study Along Home Page.
• The home page should follow this format:
• * Logo
• * Nav Bar
• • Buy (The Home Page)
• • About
• • Contact
• * Main Content
• • Home page content detailed in attachment
• * Footer
• • Copyright notice
• • Links to other stuff we do ( net-pivot.example | marlonpeake.example | BeyondTheGrid.example )
Nice to have
• It would be nice to have a book as part of the home page content.
Should not have
• Please do not use the same color scheme as BeyondTheGrid.example or Plumvane.example or QueryTheMaven.example

```html
<!DOCTYPE html>
<html lang="en">
<head>
<meta charset="utf-8">
<title>StudyAlong – Programming Books</title>
<link href="https://fonts.googleapis.com/css2?family=Raleway:wght@400;500;600&family=Josefin+Sans:wght@600&family=Open+Sans:ital,wght@0,400;1,400&display=swap" rel="stylesheet">
<style>
:root{
  --red:#dc3040;
  --gold:#f5a623;
  --grey-bar:#e6e6e6;
  --text:#444;
  --muted:#777;
  --row-a:#f5f5f5;
  --row-b:#ececec;
  --line:#dcdcdc;
  --blue:#0d5fd0;
  --blue-dark:#0a3f93;
  --orange:#ff9f0a;
  --white:#fff;
}
*{box-sizing:border-box;margin:0;padding:0}
html,body{width:894px;height:1200px;overflow:hidden;background:var(--white)}
body{position:relative;font-family:"Raleway",sans-serif;color:var(--text)}
.topbar{position:absolute;left:0;top:0;width:894px;height:23px;background:var(--grey-bar)}
.topbar-call{position:absolute;right:59px;top:5px;font:italic 10px "Open Sans",sans-serif;color:#555}
.brand{position:absolute;left:62px;top:38px;display:flex;flex-direction:column;align-items:center;width:114px}
.brand-mark{width:44px;height:44px;background:var(--red)}
.brand-name{margin-top:10px;font:600 15px "Raleway",sans-serif;color:var(--red);letter-spacing:.5px;white-space:nowrap}
.nav{position:absolute;left:0;top:133px;width:894px;height:40px;background:var(--red)}
.nav a{position:absolute;top:12px;transform:translateX(-50%);font:500 13px "Raleway",sans-serif;color:var(--white);text-decoration:none;white-space:nowrap}
.hero{position:absolute;left:0;top:173px;width:894px;height:316px;
  background:linear-gradient(100deg,#5a3a2c 0%,#b06a48 30%,#7a4634 55%,#c7835c 80%,#8c5a44 100%)}
.hero-title{position:absolute;left:431px;top:78px;font:600 36px/41px "Josefin Sans",sans-serif;color:var(--white)}
.hero-title span{color:var(--gold)}
.section-title{position:absolute;left:0;width:894px;text-align:center;font:400 21px "Raleway",sans-serif;color:#444}
.rule{position:absolute;height:1px;background:#999}
.intro{position:absolute;left:55px;top:563px;width:784px;text-align:center;font:400 11.5px/20.7px "Raleway",sans-serif;color:var(--muted)}
.tab{position:absolute;top:764px;width:196px;height:41px;background:var(--red);color:var(--white);font:500 14px/41px "Raleway",sans-serif;padding-left:12px}
.tab.center{text-align:center;padding-left:0}
.tab-pointer{position:absolute;left:141px;top:805px}
.products{position:absolute;left:57px;top:819px;width:788px;height:206px;border:1px solid var(--line);padding:3px}
.row{position:relative;height:50px;display:flex}
.row:nth-child(odd){background:var(--row-a)}
.row:nth-child(even){background:var(--row-b)}
.row+.row{border-top:1px solid var(--white)}
.cell{height:100%;display:flex;align-items:center;border-right:2px solid var(--white);font-size:12px;color:#666}
.cell.name{width:173px;padding-left:18px}
.cell.price{width:94px;justify-content:center}
.cell.buy{width:133px;justify-content:center}
.cell.shop{flex:1;padding-left:36px;border-right:none}
.btn-buy{width:94px;height:26px;border-radius:13px;background:var(--blue);border:2px solid var(--blue-dark);color:var(--white);font:500 10.5px/22px "Raleway",sans-serif;text-align:center}
.btn-shop{width:117px;height:34px;background:var(--orange);color:var(--white);font:600 12px/34px "Raleway",sans-serif;text-align:center}
.footer{position:absolute;left:0;top:1093px;width:894px;height:107px;background:var(--red);color:var(--white)}
.footer-label{position:absolute;left:60px;top:19px;font:400 11px "Open Sans",sans-serif}
.partner-badge{position:absolute;left:59px;top:37px;width:235px;height:47px;background:var(--white);border:1px solid #ccc}
.copyright{position:absolute;right:52px;top:48px;font:400 11px "Open Sans",sans-serif}
</style>
</head>
<body>
<div class="topbar"><span class="topbar-call">Call us &nbsp;1-800-555-0142</span></div>

<div class="brand">
  <div class="brand-mark"></div>
  <div class="brand-name">STUDY - ALONG</div>
</div>

<nav class="nav">
  <a style="left:278px">HOME</a>
  <a style="left:363px">BUY</a>
  <a style="left:459px">ABOUT US</a>
  <a style="left:580px">CONTACT US</a>
</nav>

<section class="hero" role="img" aria-label="Photo of hands holding a tablet in warm light">
  <h1 class="hero-title">KNOWLEDGE TO BOOST<br><span>YOUR CAREER</span></h1>
</section>

<h2 class="section-title" style="top:513px">Welcome to StudyAlong</h2>
<div class="rule" style="left:350px;top:545px;width:166px"></div>
<p class="intro">Lorem ipsum dolor sit amet, consectetuer adipiscing elit. Aenean commodo ligula eget dolor. Aenean massa. Cum sociis&nbsp; natoque penatibus et magnis<br>Lorem ipsum dolor sit amet, consectetuer adipiscing elit. Aenean commodo ligula eget&nbsp; dolor. Aenean massa. Cum sociis natoque<br>penatibus et magnisdolor sit amet, consectetuer adipiscing elit &nbsp; Aenean commodo ligula eget dolor. Aenean massa. Cum socii<br>natoque penatibus et magnis dolor sit amet consectetuer adipiscing elit.Aenean commodo ligula eget dolor. Aenean massa.<br>Cum sociis natoque penatibus et magnis .</p>

<h2 class="section-title" style="top:700px">Our Products</h2>
<div class="rule" style="left:397px;top:730px;width:79px"></div>

<div class="tab" style="left:58px">HelixJS 1.5 &amp; Scaffold</div>
<div class="tab" style="left:267px">HelixJS 2 &amp; Scaffold</div>
<div class="tab center" style="left:478px">PulseJS</div>
<svg class="tab-pointer" width="18" height="9" viewBox="0 0 18 9"><path d="M0 0H18L9 9Z" fill="#dc3040"/></svg>

<div class="products">
  <div class="row"><div class="cell name">With Mock Services</div><div class="cell price">$5.99</div><div class="cell buy"><div class="btn-buy">BUY FROM US</div></div><div class="cell shop"><div class="btn-shop">Buy from Shopvale</div></div></div>
  <div class="row"><div class="cell name">With BranchJS Services</div><div class="cell price">$5.99</div><div class="cell buy"><div class="btn-buy">BUY FROM US</div></div><div class="cell shop"><div class="btn-shop">Buy from Shopvale</div></div></div>
  <div class="row"><div class="cell name">With FrostScript Services</div><div class="cell price">$5.99</div><div class="cell buy"><div class="btn-buy">BUY FROM US</div></div><div class="cell shop"><div class="btn-shop">Buy from Shopvale</div></div></div>
  <div class="row"><div class="cell name">Buy Them All</div><div class="cell price">$9.99</div><div class="cell buy"><div class="btn-buy">BUY FROM US</div></div><div class="cell shop"><div class="btn-shop">Buy from Shopvale</div></div></div>
</div>

<footer class="footer">
  <span class="footer-label">Partners</span>
  <div class="partner-badge" role="img" aria-label="Partner badge"></div>
  <span class="copyright">2016@study-along.example. All Rights Reserved.</span>
</footer>
</body>
</html>
```